Vorn upkeep KT Solar Venture

Solar power system install
Services and maintenance
wiring, Rewinding and Renovation
Switch Board Upgrade
Power and lighting point
t doesn’t matter how much you spend on quality parts, your solar system will let you down if your design and installation are sub-par. Have your solar system tailored and installed by our Master Electrician and Bright Grid Guild Accredited team.

Target Market(s)

sales and installed

Industry/Entity Type

Solar install and retailer

Contact Information for Business Card

Name , Email, Phone Number ,Business address,

Font styles to use
Serif

Colors
0054AA
0677BA
7BADD7
CADEEF
E8F1F8

Requirements
Must have
• clear and bright
Nice to have
• new design
Should not have
• unclear pictures

```html
<!DOCTYPE html>
<html lang="en">
<head>
<meta charset="utf-8">
<title>Vorn Upkeep · KT Solar Venture — Business Card</title>
<link href="https://fonts.googleapis.com/css2?family=Roboto:wght@400;500;700&display=swap" rel="stylesheet">
<style>
  :root {
    --backdrop: #2e2e2e;
    --card: #ececec;
    --card-edge: #f6f6f6;
    --brand-blue: #0054aa;
    --mid-blue: #0677ba;
    --leaf-green: #3f9a2f;
    --band-green: #6aae3c;
    --ink: #1c1c1c;
    --band-text: #eef6ee;
  }
  * { margin: 0; padding: 0; box-sizing: border-box; }
  html, body { width: 1200px; height: 1138px; overflow: hidden; }
  body {
    background: var(--backdrop);
    font-family: "Roboto", Arial, sans-serif;
    color: var(--ink);
    position: relative;
  }
  .card {
    position: absolute;
    left: 170px;
    width: 860px;
    height: 518px;
    border-radius: 22px;
    background: linear-gradient(160deg, var(--card-edge), var(--card) 60%, #e2e2e2);
    overflow: hidden;
  }
  .card--front { top: 36px; }
  .card--back { top: 584px; }

  .brand { position: absolute; display: flex; align-items: center; gap: 22px; }
  .brand__dot {
    width: 120px; height: 120px; border-radius: 50%;
    background: linear-gradient(135deg, #f2b01e, var(--leaf-green) 55%, var(--mid-blue));
    flex: none;
  }
  .brand__name {
    font-weight: 700;
    color: var(--brand-blue);
    font-size: 46px;
    line-height: 1.05;
    letter-spacing: 1px;
    text-transform: uppercase;
  }
  .card--front .brand { left: 140px; top: 70px; }
  .card--back .brand { left: 18px; top: 40px; }

  .services {
    position: absolute; left: 0; right: 0; top: 328px; height: 103px;
    background: linear-gradient(90deg, var(--band-green), #3d9a6a 45%, var(--mid-blue));
    color: var(--band-text);
    font-size: 22px;
    text-align: center;
    display: flex; flex-direction: column; justify-content: center; gap: 6px;
  }
  .services .sep { margin: 0 10px; }

  .site {
    position: absolute; left: 0; right: 0; top: 458px;
    display: flex; align-items: center; justify-content: center; gap: 32px;
    font-size: 21px;
  }
  .site__rule { width: 110px; height: 3px; }
  .site__rule--blue { background: linear-gradient(90deg, transparent, var(--mid-blue)); }
  .site__rule--green { background: linear-gradient(90deg, var(--band-green), transparent); }

  .person { position: absolute; left: 47px; top: 280px; }
  .person__name { font-size: 34px; font-weight: 700; color: var(--brand-blue); line-height: 40px; }
  .person__role { font-size: 21px; line-height: 26px; margin-top: 4px; }

  .divider { position: absolute; left: 42px; top: 332px; }
  .scenery {
    position: absolute; left: 672px; top: 284px; width: 150px; height: 54px;
    background: linear-gradient(90deg, rgba(106,174,60,0.12), rgba(106,174,60,0.4));
    border-radius: 6px;
  }

  .contacts { position: absolute; left: 47px; top: 388px; list-style: none; font-size: 21px; }
  .contacts li { display: flex; align-items: center; gap: 22px; height: 33px; }
  .contacts svg { width: 20px; height: 20px; fill: var(--leaf-green); }

  .address {
    position: absolute; right: 45px; top: 421px;
    text-align: right; font-size: 21px; line-height: 33px;
  }
</style>
</head>
<body>

<section class="card card--front">
  <div class="brand">
    <span class="brand__dot"></span>
    <div class="brand__name">Vorn Upkeep<br>KT Solar Venture</div>
  </div>
  <div class="services">
    <p>Solar Power System Install<span class="sep">|</span>Wiring, Rewinding &amp; Renovation</p>
    <p>Services &amp; Maintenance<span class="sep">|</span>Switch Board Upgrade<span class="sep">|</span>Power &amp; Lighting Point</p>
  </div>
  <div class="site">
    <span class="site__rule site__rule--blue"></span>
    <span>www.ktsolarventure.com</span>
    <span class="site__rule site__rule--green"></span>
  </div>
</section>

<section class="card card--back">
  <div class="brand">
    <span class="brand__dot"></span>
    <div class="brand__name">Vorn Upkeep<br>KT Solar Venture</div>
  </div>

  <div class="person">
    <p class="person__name">John Doe Smith</p>
    <p class="person__role">Managing Director</p>
  </div>

  <svg class="divider" width="800" height="40" viewBox="0 0 800 40" aria-hidden="true">
    <path d="M0 35 H270 C315 35 300 12 350 12 H770 C785 12 795 6 798 0" fill="none" stroke="#6aae3c" stroke-width="3"/>
  </svg>
  <div class="scenery" role="img" aria-label="Small wind turbines and a leaf on a green line"></div>

  <ul class="contacts">
    <li>
      <svg viewBox="0 0 24 24" aria-hidden="true"><path d="M6.6 10.8a15 15 0 0 0 6.6 6.6l2.2-2.2a1 1 0 0 1 1-.25 11.4 11.4 0 0 0 3.6.57 1 1 0 0 1 1 1V20a1 1 0 0 1-1 1A17 17 0 0 1 3 4a1 1 0 0 1 1-1h3.5a1 1 0 0 1 1 1c0 1.25.2 2.45.57 3.57a1 1 0 0 1-.25 1z"/></svg>
      <span>828-111-1111</span>
    </li>
    <li>
      <svg viewBox="0 0 24 24" aria-hidden="true"><path d="M2 5h20v14H2zm2 2v.5l8 5 8-5V7zm0 3v7h16v-7l-8 5z"/></svg>
      <span>john@yourwebsite.com</span>
    </li>
    <li>
      <svg viewBox="0 0 24 24" aria-hidden="true"><path d="M12 2a10 10 0 1 0 0 20 10 10 0 0 0 0-20zm6.9 6h-3a15 15 0 0 0-1.4-3.9A8 8 0 0 1 18.9 8zM12 4c.8 1.2 1.5 2.5 1.9 4h-3.8c.4-1.5 1.1-2.8 1.9-4zM4.3 14a8 8 0 0 1 0-4h3.4a16 16 0 0 0 0 4zm.8 2h3a15 15 0 0 0 1.4 3.9A8 8 0 0 1 5.1 16zm3-8h-3a8 8 0 0 1 4.4-3.9A15 15 0 0 0 8.1 8zM12 20c-.8-1.2-1.5-2.5-1.9-4h3.8c-.4 1.5-1.1 2.8-1.9 4zm2.3-6H9.7a14 14 0 0 1 0-4h4.6a14 14 0 0 1 0 4zm.2 5.9a15 15 0 0 0 1.4-3.9h3a8 8 0 0 1-4.4 3.9zm1.8-5.9a16 16 0 0 0 0-4h3.4a8 8 0 0 1 0 4z"/></svg>
      <span>www.yourwebsite.com</span>
    </li>
  </ul>

  <p class="address">234 Anywhere St., Any City,<br>Any Town, US 123456</p>
</section>

</body>
</html>
```